TALMORK

The business want a professional looking business card. We have a scetch we will add but want the extra upgrade, and would like more suggestions for variations of our business cards.

```html
<!DOCTYPE html>
<html lang="en">
<head>
<meta charset="utf-8">
<title>TALMORK business card</title>
<link rel="stylesheet" href="https://fonts.googleapis.com/css2?family=Cinzel:wght@500&family=Alegreya+Sans:wght@500&family=Figtree:wght@500;600&display=swap">
<style>
  :root {
    --backdrop: #958566;
    --card-dark: #1a1005;
    --card-warm: #3a2a0e;
    --gold: #d9aa45;
    --gold-light: #f6d27e;
    --gold-deep: #8a6410;
    --text-light: #efe7d7;
    --text-muted: #d4cdbf;
  }
  * { margin: 0; padding: 0; box-sizing: border-box; }
  html, body { width: 1200px; height: 1200px; overflow: hidden; }
  body { background: var(--backdrop); position: relative; font-family: "Figtree", sans-serif; }

  .card {
    position: absolute;
    left: 180px;
    width: 840px;
    height: 480px;
    overflow: hidden;
  }
  .card--front {
    top: 78px;
    background: linear-gradient(90deg, var(--card-warm) 0%, var(--card-warm) 48%, var(--card-dark) 58%, var(--card-dark) 100%);
  }
  .card--back {
    top: 630px;
    background: linear-gradient(90deg, var(--card-dark) 0%, var(--card-dark) 48%, var(--card-warm) 62%, var(--card-warm) 100%);
  }
  .card__edge {
    position: absolute;
    top: 0; right: 0;
    width: 18px; height: 100%;
    background: linear-gradient(180deg, var(--gold-light), var(--gold) 45%, var(--gold-deep));
  }

  .ornament-area { position: absolute; }
  .card--front .ornament-area {
    left: 0; top: 0;
    width: 430px; height: 480px;
    background: radial-gradient(ellipse 60% 55% at 40% 50%, rgba(246, 210, 126, 0.55), rgba(217, 170, 69, 0.28) 55%, rgba(138, 100, 16, 0) 100%);
  }
  .card--back .ornament-area {
    left: 0; top: 0;
    width: 224px; height: 226px;
    background: radial-gradient(ellipse 65% 65% at 30% 30%, rgba(246, 210, 126, 0.45), rgba(217, 170, 69, 0.2) 55%, rgba(138, 100, 16, 0) 100%);
  }

  .brand { position: absolute; text-align: center; }
  .brand__dot {
    display: block;
    width: 56px; height: 56px;
    margin: 0 auto 50px;
    border-radius: 50%;
    background: var(--gold);
  }
  .brand__name {
    font-family: "Cinzel", serif;
    font-weight: 500;
    font-size: 46px;
    letter-spacing: 0.18em;
    color: var(--gold);
    line-height: 1;
    margin-right: -0.18em;
  }
  .brand__since {
    font-family: "Figtree", sans-serif;
    font-weight: 600;
    font-size: 14px;
    letter-spacing: 0.42em;
    color: var(--gold);
    margin-top: 10px;
    margin-right: -0.42em;
  }
  .card--front .brand { left: 444px; top: 184px; width: 320px; }
  .card--back .brand { left: 376px; top: 82px; width: 320px; }
  .card--back .brand__since { margin-top: 8px; }

  .person {
    position: absolute;
    right: 486px;
    top: 236px;
    text-align: right;
  }
  .person__name {
    font-family: "Alegreya Sans", sans-serif;
    font-weight: 500;
    font-size: 58px;
    line-height: 64px;
    background: linear-gradient(180deg, var(--gold-light), var(--gold) 55%, var(--gold-deep));
    -webkit-background-clip: text;
    background-clip: text;
    color: transparent;
  }
  .person__role {
    font-size: 20px;
    font-weight: 500;
    color: var(--text-muted);
    margin-top: 16px;
  }
  .rule {
    position: absolute;
    left: 374px; top: 397px;
    width: 314px; height: 1px;
    background: var(--gold);
  }

  .contact { position: absolute; left: 402px; top: 237px; list-style: none; }
  .contact__item {
    display: flex; align-items: center; gap: 16px;
    height: 46px;
    font-size: 23.5px; font-weight: 600;
    color: var(--text-light);
  }
  .contact__icon { width: 24px; height: 24px; flex: none; }
</style>
</head>
<body>

<section class="card card--front">
  <div class="ornament-area" role="img" aria-label="Large gold foil decorative motif"></div>
  <div class="brand">
    <span class="brand__dot"></span>
    <div class="brand__name">TALMORK</div>
    <div class="brand__since">SINCE 2026</div>
  </div>
  <div class="card__edge"></div>
</section>

<section class="card card--back">
  <div class="ornament-area" role="img" aria-label="Gold foil decorative motif in the corner"></div>
  <div class="brand">
    <div class="brand__name">TALMORK</div>
    <div class="brand__since">SINCE 2026</div>
  </div>

  <div class="person">
    <div class="person__name">Erik Anders<br>Holmvik</div>
    <div class="person__role">CEO &amp; Founder</div>
  </div>
  <div class="rule"></div>

  <ul class="contact">
    <li class="contact__item">
      <svg class="contact__icon" viewBox="0 0 24 24"><path fill="#d9aa45" d="M6.6 10.8a15 15 0 0 0 6.6 6.6l2.2-2.2a1 1 0 0 1 1-.25 11.4 11.4 0 0 0 3.6.57 1 1 0 0 1 1 1V20a1 1 0 0 1-1 1A17 17 0 0 1 3 4a1 1 0 0 1 1-1h3.5a1 1 0 0 1 1 1c0 1.25.2 2.45.57 3.57a1 1 0 0 1-.25 1z"/></svg>
      <span>004791234567</span>
    </li>
    <li class="contact__item">
      <svg class="contact__icon" viewBox="0 0 24 24"><path fill="#d9aa45" d="M3 5h18v14H3z"/><path fill="none" stroke="#1a1005" stroke-width="1.6" d="M3 6l9 7 9-7"/></svg>
      <span>talmork.llc@mailbox.com</span>
    </li>
    <li class="contact__item">
      <svg class="contact__icon" viewBox="0 0 24 24" fill="none" stroke="#d9aa45" stroke-width="1.6"><circle cx="12" cy="12" r="9"/><ellipse cx="12" cy="12" rx="4" ry="9"/><path d="M3 12h18M5 7h14M5 17h14"/></svg>
      <span>www.talmork.llc</span>
    </li>
  </ul>
  <div class="card__edge"></div>
</section>

</body>
</html>
```